Business Card for premium dental clinic

We are a premium dental clinic based in Brasov, Romania with more than 15 year on the market, providing quality dental treatment made by a team of more specialized dentists, working with modern equipment as a solution to beautiful and healthy teeth.

Our current logo for the clinic use 2 square with colors black and gold - dr Ternisu - studio, using family fonts Bodoni, Myriad Pro and Segoe Print.
Depending on the printing we used some gold CMYK background or gold foil picture background or a gold gradient.
We want a business card:
- eye catching business card
- distinguished business card
- premium design
- to keep the color scheme of black and gold
- to attract the customers to spent time reading the information
- modern concept

```html
<!DOCTYPE html>
<html lang="en">
<head>
<meta charset="utf-8">
<title>Ternisu Studio – Business Card</title>
<link rel="stylesheet" href="https://fonts.googleapis.com/css2?family=Roboto+Condensed:wght@400&family=Roboto:wght@400&display=swap">
<style>
  :root {
    --backdrop: #3a3a3a;
    --card-black: #232323;
    --gold-light: #f6d64a;
    --gold-mid: #e2b21c;
    --gold-deep: #b88a0c;
    --ink: #151515;
    --paper: #ffffff;
    --text-light: #f2f2f2;
  }
  * { margin: 0; padding: 0; box-sizing: border-box; }
  html, body { width: 799px; height: 1200px; overflow: hidden; }
  body {
    background: var(--backdrop);
    font-family: "Roboto Condensed", "Arial Narrow", sans-serif;
    position: relative;
  }
  .card {
    position: absolute;
    left: 60px;
    width: 680px;
    height: 390px;
    background: var(--card-black);
    overflow: hidden;
    box-shadow: 0 10px 28px rgba(0,0,0,.45);
  }
  .card--front { top: 100px; }
  .card--back  { top: 700px; }

  .gold-foil {
    background: linear-gradient(135deg, var(--gold-light) 0%, var(--gold-mid) 45%, var(--gold-deep) 70%, var(--gold-light) 100%);
  }

  /* Front */
  .front-foil {
    position: absolute; left: 0; top: 0;
    width: 300px; height: 100%;
  }
  .name-plate {
    position: absolute; left: 36px; top: 95px;
    width: 250px; height: 106px;
    background: var(--paper);
    display: flex; align-items: center; justify-content: center;
    color: var(--ink);
  }
  .name-plate .title { font-size: 34px; align-self: flex-start; margin-top: 28px; }
  .name-plate .surname { font-size: 60px; letter-spacing: -1px; }

  .brand {
    position: absolute;
    color: var(--text-light);
    font-family: "Roboto Condensed", "Arial Narrow", sans-serif;
    font-weight: 400;
    line-height: 1;
  }
  .brand .brand-name { display: block; }
  .brand .brand-tag  { display: block; }
  .card--front .brand { left: 380px; top: 125px; }
  .card--front .brand-name { font-size: 66px; padding-left: 40px; }
  .card--front .brand-tag  { font-size: 40px; margin-top: 26px; }

  /* Back */
  .back-plate {
    position: absolute; left: 40px; top: 40px;
    width: 220px; height: 84px;
    display: flex; align-items: center; justify-content: center;
    color: var(--ink);
  }
  .back-plate .title { font-size: 24px; align-self: flex-start; margin-top: 22px; }
  .back-plate .surname { font-size: 46px; letter-spacing: -1px; }

  .contact {
    position: absolute; left: 40px; top: 150px;
    list-style: none;
    font-family: "Roboto", Arial, sans-serif;
    color: var(--text-light);
    font-size: 15px;
    line-height: 22px;
  }
  .contact li { display: flex; align-items: flex-start; gap: 10px; }
  .contact .icon { width: 14px; height: 14px; margin-top: 4px; flex: none; }
  .contact .address { padding-left: 24px; }

  .card--back .brand { left: 395px; top: 95px; }
  .card--back .brand-name { font-size: 52px; }
  .card--back .brand-tag  { font-size: 32px; margin-top: 18px; padding-left: 100px; }
</style>
</head>
<body>

  <section class="card card--front" aria-label="Card front">
    <div class="front-foil gold-foil" role="img" aria-label="Gold foil texture background"></div>
    <div class="name-plate">
      <span class="title">dr.</span><span class="surname">ternisu</span>
    </div>
    <div class="brand">
      <span class="brand-name">studio</span>
      <span class="brand-tag">dental clinic</span>
    </div>
  </section>

  <section class="card card--back" aria-label="Card back">
    <div class="back-plate gold-foil" role="img" aria-label="Gold foil name plate">
      <span class="title">dr.</span><span class="surname">ternisu</span>
    </div>

    <ul class="contact">
      <li>
        <svg class="icon" viewBox="0 0 14 14" aria-hidden="true"><path fill="#e2b21c" d="M3 1l2.5 2.8-1.3 1.6c.8 1.7 2 2.9 3.7 3.7l1.6-1.3L12.3 10.3 11 13C5.5 12.5 1.5 8.5 1 3z"/></svg>
        <span>828-555-0147</span>
      </li>
      <li>
        <svg class="icon" viewBox="0 0 14 14" aria-hidden="true"><rect x="1" y="3" width="12" height="8.5" fill="#e2b21c"/><path d="M1.5 3.5L7 8l5.5-4.5" fill="none" stroke="#232323" stroke-width="1.2"/></svg>
        <span>hello@ternisustudio.com</span>
      </li>
      <li>
        <svg class="icon" viewBox="0 0 14 14" aria-hidden="true"><circle cx="7" cy="7" r="6" fill="#e2b21c"/><path d="M1 7h12M7 1c-3 3.3-3 8.7 0 12M7 1c3 3.3 3 8.7 0 12" fill="none" stroke="#232323" stroke-width=".9"/></svg>
        <span>www.ternisustudio.com</span>
      </li>
      <li class="address">18 Livezii St., Brasov,</li>
      <li class="address">Brasov County, RO 500123</li>
    </ul>

    <div class="brand">
      <span class="brand-name">studio</span>
      <span class="brand-tag">dental clinic</span>
    </div>
  </section>

</body>
</html>
```